Provide bookkeeping and accounting services to small and growing businesses

We need website and logo design using the name Dornaby as the logo.
The target audience are small companies and startups who need:
1) Simple bookkeeping services
2) Accounting advice that only someone with many years of senior financial experience as a CPA can provide.

The services are provided by two individuals. each of whom specialize in one of the areas.

We want the website to be clean without a lot of visual distraction but don't know how to make a boring subject interesting. We believe our potential clients, small business owners, need to find what they want quickly and easily without a lot of verbiage or distractions.

We've attached a draft of the homepage and have completed the text on most of the other pages.

Target Market(s)

small and early stage growth companies in San Diego North County

Industry/Entity Type

Accounting

Number of Pages Required

1 page

Font styles to use
Sans Serif

Colors
86cfc6
33b8a4
85cae6

Requirements
Must have
• We need a design for the website homepage that includes the name Dornaby as the logo. Must include a design for the name.
• Must have color in teal or greenish blue.
Nice to have
• White background, clean, clear, uncluttered.
• We would like to use the design in a Theme on a WordPress website. Themes Paper Lantern and Quiet Harbour are appealing to us.
Should not have
• Moving pictures

```html
<!DOCTYPE html>
<html lang="en">
<head>
<meta charset="utf-8">
<title>Dornaby Bookkeeping</title>
<link rel="stylesheet" href="https://fonts.googleapis.com/css2?family=Raleway:wght@400;500;600;700&family=Oxygen:wght@300;400;700&family=Lato:ital,wght@0,400;0,700;1,400&display=swap">
<style>
:root{
  --teal:#33b8a4;
  --teal-soft:#86cfc6;
  --teal-btn:#7fcdc3;
  --sky:#85cae6;
  --navy:#12384a;
  --ink:#2b2b2b;
  --body:#333;
  --muted:#666;
  --line:#cfcfcf;
  --grey-bg:#f3f3f3;
  --partner-bg:#eff8fb;
  --footer:#333333;
  --footer-dark:#2a2a2a;
  --white:#fff;
}
*{box-sizing:border-box;margin:0;padding:0}
html,body{width:1200px;height:2439px;overflow:hidden}
body{position:relative;background:var(--white);font-family:"Raleway",Arial,sans-serif;color:var(--body)}
.abs{position:absolute}
a{color:inherit;text-decoration:none}

/* top bar */
.top-bar{position:absolute;left:0;top:0;width:1200px;height:33px;background:var(--navy);color:var(--white);font-family:"Lato",sans-serif;font-weight:700;font-size:14px}
.top-bar .item{position:absolute;top:8px;display:flex;align-items:center;gap:8px}
.top-bar svg{width:18px;height:18px}

/* header */
.site-header{position:absolute;left:0;top:33px;width:1200px;height:86px;background:var(--white)}
.logo{position:absolute;left:101px;top:14px}
.logo-name{font-family:"Raleway",sans-serif;font-weight:700;font-size:38px;line-height:38px;color:var(--teal);letter-spacing:0.5px}
.logo-tag{font-family:"Raleway",sans-serif;font-weight:600;font-size:14px;letter-spacing:6.5px;color:var(--ink);margin-top:4px}
.main-nav{position:absolute;top:29px;left:474px;display:flex}
.main-nav a{font-size:14px;color:var(--ink);padding:7px 0;height:30px;display:block}
.main-nav a.active{background:var(--teal);color:var(--white);padding:7px 12px;font-weight:600}

/* hero */
.hero{position:absolute;left:0;top:119px;width:1200px;height:515px;background:linear-gradient(135deg,#5f6b77 0%,#9aa3ad 40%,#c9cfd4 65%,#7c8690 100%)}
.hero-shade{position:absolute;inset:0;background:rgba(40,55,70,0.35)}
.hero h1{position:absolute;left:0;width:1200px;top:232px;text-align:center;font-family:"Raleway",sans-serif;font-weight:500;font-size:33px;color:#80d3c8}
.hero p{position:absolute;left:0;width:1200px;top:288px;text-align:center;font-weight:600;font-size:16px;color:var(--white)}
.hero-arrow{position:absolute;top:240px;width:34px;height:34px}

/* section headings */
.section-title{position:absolute;left:0;width:1200px;text-align:center;font-family:"Oxygen",sans-serif;font-weight:400;font-size:31px;color:var(--ink)}
.section-title span,.col-title span{color:var(--teal)}
.divider{position:absolute;height:10px}
.divider::before{content:"";position:absolute;left:0;right:0;top:5px;height:1px;background:var(--line)}
.dots{position:absolute;left:50%;top:0;transform:translateX(-50%);display:flex;gap:6px;padding:0 8px}
.dots i{display:block;width:9px;height:9px;border-radius:50%;border:1px solid #aaa;background:var(--white)}
.dots i.on{background:#aaa}

.btn{position:absolute;background:var(--teal-btn);color:var(--white);font-weight:600;font-size:15px;text-align:center;border-radius:2px}

/* about */
.about-text{position:absolute;left:110px;width:980px;top:752px;text-align:center;font-size:13px;line-height:24.5px;color:#222;font-weight:500}

/* services */
.services{position:absolute;left:0;top:924px;width:1200px;height:453px;background:var(--grey-bg)}
.service{position:absolute;top:140px;width:250px;text-align:center}
.service-icon{width:110px;height:110px;margin:0 auto;border-radius:50%;background:#fafafa;box-shadow:0 2px 6px rgba(0,0,0,.12);display:flex;align-items:center;justify-content:center}
.service-icon .inner{width:92px;height:92px;border-radius:50%;background:var(--white);display:flex;align-items:center;justify-content:center}
.service h3{margin-top:36px;font-size:16px;font-weight:700;color:var(--ink)}
.service p{margin-top:13px;font-size:13px;line-height:22px;color:#555}
.service .btn{position:relative;display:inline-block;width:112px;height:33px;line-height:33px;margin-top:12px}
.service-sep{position:absolute;top:150px;width:1px;height:200px;background:linear-gradient(#f3f3f3,#ddd,#f3f3f3)}

/* testimonials & contact */
.col-title{position:absolute;font-family:"Oxygen",sans-serif;font-weight:400;font-size:31px;color:var(--ink)}
.quote-card{position:absolute;left:101px;top:1520px;width:512px;height:228px;background:#fafafa;border:1px solid #e3e3e3;border-radius:6px;box-shadow:0 2px 4px rgba(0,0,0,.08)}
.quote-card p{position:absolute;left:22px;top:26px;width:470px;font-family:"Lato",sans-serif;font-style:italic;font-size:13px;line-height:24.5px;color:#333;text-indent:24px}
.quote-mark{position:absolute;font-family:"Lato",sans-serif;font-size:56px;line-height:1;color:#cfe9e5;font-style:italic}
.quote-close{font-family:"Lato",sans-serif;font-size:40px;line-height:0;color:#cfe9e5;vertical-align:-14px;margin-left:6px}
.avatar{position:absolute;left:122px;top:1707px;width:114px;height:114px;border-radius:50%;background:#fff;box-shadow:0 1px 5px rgba(0,0,0,.2);display:flex;align-items:center;justify-content:center}
.avatar div{width:100px;height:100px;border-radius:50%;background:linear-gradient(160deg,#9fb7cc,#5d7c99)}
.client-name{position:absolute;left:260px;top:1775px;font-weight:700;font-size:15px;color:var(--teal)}
.v-dash{position:absolute;left:686px;top:1504px;height:302px;border-left:1px dashed #ccc}
.field{position:absolute;left:758px;width:341px;height:34px;border:1px solid #c9c9c9;background:var(--white);font-size:13px;padding:9px 10px;color:#222}

/* partners */
.partners{position:absolute;left:0;top:1862px;width:1200px;height:296px;background:var(--partner-bg)}
.partner{position:absolute;top:140px;width:179px;height:100px;background:var(--white);border:1px solid #e6e6e6;display:flex;align-items:center;justify-content:center}
.partner .badge{width:100px;height:30px;background:#d7dadc;border-radius:3px}

/* footer */
.footer{position:absolute;left:0;top:2158px;width:1200px;height:232px;background:var(--footer);color:#ddd}
.footer h4{position:absolute;top:30px;font-family:"Oxygen",sans-serif;font-weight:400;font-size:17px;color:var(--white);padding-bottom:8px;border-bottom:1px solid #555}
.quick-links{position:absolute;list-style:none;font-size:13px;line-height:24.5px}
.quick-links li::before{content:"›";margin-right:8px}
.footer .text{position:absolute;font-size:13px;line-height:21px}
.f-sep{position:absolute;top:30px;width:1px;height:180px;background:#444}
.newsletter-art{position:absolute;left:760px;top:84px;width:64px;height:48px;border-radius:4px;background:linear-gradient(135deg,#e8e8e8,#9a9a9a)}
.newsletter-input{position:absolute;left:611px;top:148px;width:156px;height:32px;background:var(--white);font-size:12px;color:#333;padding:8px 10px 0 30px}
.newsletter-btn{position:absolute;left:767px;top:148px;width:98px;height:32px;background:var(--teal);color:var(--white);font-weight:700;font-size:13px;text-align:center;line-height:32px}
.social{position:absolute;left:992px;list-style:none;font-size:10px;font-weight:700;letter-spacing:.5px}
.social li{display:flex;align-items:center;gap:12px;height:36px}
.social i{display:block;width:14px;height:14px;background:#eee;border-radius:2px}
.bottom-bar{position:absolute;left:0;top:2390px;width:1200px;height:49px;background:var(--footer-dark);border-top:1px solid #444;color:#ccc;font-size:13px}
</style>
</head>
<body>

<div class="top-bar">
  <div class="item" style="left:718px">
    <svg viewBox="0 0 18 18"><circle cx="9" cy="9" r="9" fill="#fff"/><rect x="4.5" y="6" width="9" height="6.5" fill="#12384a"/><path d="M4.5 6 9 9.5 13.5 6" stroke="#fff" fill="none"/></svg>
    <span>info@dornabybooks.net</span>
  </div>
  <div class="item" style="left:975px">
    <svg viewBox="0 0 18 18"><circle cx="9" cy="9" r="8" fill="none" stroke="#fff" stroke-width="1.5"/><path d="M6 5.5c0 4 2.5 6.5 6.5 6.5l.5-1.5-2-1-1 1c-1-.5-2-1.5-2.5-2.5l1-1-1-2z" fill="#fff"/></svg>
    <span>555-014-2288</span>
  </div>
</div>

<header class="site-header">
  <div class="logo">
    <div class="logo-name">Dornaby</div>
    <div class="logo-tag">BOOKKEEPING</div>
  </div>
  <nav class="main-nav">
    <a class="active">Home</a>
    <a style="margin-left:34px">About Us</a>
    <a style="margin-left:47px">Services</a>
    <a style="margin-left:45px">Experience</a>
    <a style="margin-left:47px">Resources</a>
    <a style="margin-left:47px">Contact Us</a>
  </nav>
</header>

<section class="hero">
  <div class="hero-image" role="img" aria-label="Close-up photo of a calculator and pen resting on a printed ledger of figures" style="position:absolute;inset:0"></div>
  <div class="hero-shade"></div>
  <svg class="hero-arrow" style="left:39px" viewBox="0 0 34 34"><circle cx="17" cy="17" r="16" fill="none" stroke="#fff" stroke-width="1.5"/><path d="M19.5 11 13.5 17l6 6" fill="none" stroke="#fff" stroke-width="2"/></svg>
  <svg class="hero-arrow" style="left:1127px" viewBox="0 0 34 34"><circle cx="17" cy="17" r="16" fill="none" stroke="#fff" stroke-width="1.5"/><path d="M14.5 11l6 6-6 6" fill="none" stroke="#fff" stroke-width="2"/></svg>
  <h1>Accounting And Bookkeeping Services And Support</h1>
  <p>For Small And Growing Organizations In San Diego North County</p>
</section>

<section class="about">
  <h2 class="section-title" style="top:672px">About <span>Dornaby Bookkeeping</span></h2>
  <div class="divider" style="left:438px;width:370px;top:720px"><div class="dots" style="background:var(--white)"><i></i><i class="on"></i><i></i></div></div>
  <p class="about-text">Lorem ipsum dolor sit amet, consectetur adipiscing elit, sed do eiusmod tempor incididunt ut labore et dolore magna aliqua. Ut enim ad minim veniam, quis nostrud exercitation ullamco laboris nisi ut aliquip ex ea commodo consequat. Duis aute irure dolor in reprehenderit in voluptate velit esse cillum dolore eu fugiat nulla pariatur. Excepteur sint occaecat cupidatat non proident, sunt in culpa qui officia deserunt mollit anim id est laborum.</p>
  <div class="btn" style="left:540px;top:848px;width:111px;height:34px;line-height:34px">Read More</div>
</section>

<section class="services">
  <h2 class="section-title" style="top:36px">Our <span>Financial Services</span></h2>
  <div class="divider" style="left:434px;width:332px;top:85px"><div class="dots" style="background:var(--grey-bg)"><i></i><i class="on"></i><i></i></div></div>
  <svg class="abs" style="left:48px;top:262px" width="22" height="40" viewBox="0 0 22 40"><path d="M20 2 3 20l17 18" fill="none" stroke="#aaa" stroke-width="2"/></svg>
  <svg class="abs" style="left:1130px;top:262px" width="22" height="40" viewBox="0 0 22 40"><path d="M2 2l17 18L2 38" fill="none" stroke="#aaa" stroke-width="2"/></svg>

  <div class="service" style="left:72px">
    <div class="service-icon"><div class="inner"><svg width="44" height="44" viewBox="0 0 44 44"><rect x="10" y="6" width="26" height="32" rx="4" fill="var(--teal)"/><rect x="6" y="10" width="26" height="30" rx="4" fill="var(--teal)" stroke="#fff" stroke-width="2"/><text x="19" y="31" font-family="Raleway,sans-serif" font-weight="700" font-size="18" fill="#fff" text-anchor="middle">$</text></svg></div></div>
    <h3>BOOKKEEPING</h3>
    <p>Lorem ipsum dolor sit amet,<br>consectetur adipiscing elit, sed do</p>
    <span class="btn">Read More</span>
  </div>
  <div class="service-sep" style="left:341px"></div>
  <div class="service" style="left:335px">
    <div class="service-icon"><div class="inner"><svg width="48" height="44" viewBox="0 0 48 44"><rect x="12" y="4" width="24" height="22" fill="var(--teal)"/><path d="M4 18v22h40V18L24 30z" fill="var(--teal)"/><path d="M4 40l16-12M44 40 28 28" stroke="#fff" stroke-width="2"/><text x="24" y="21" font-family="Raleway,sans-serif" font-weight="700" font-size="14" fill="#fff" text-anchor="middle">$</text></svg></div></div>
    <h3>ACCOUNTS PAYABLE</h3>
    <p>Lorem ipsum dolor sit amet,<br>consectetur adipiscing elit, sed do</p>
    <span class="btn">Read More</span>
  </div>
  <div class="service-sep" style="left:600px"></div>
  <div class="service" style="left:599px">
    <div class="service-icon"><div class="inner"><svg width="56" height="44" viewBox="0 0 56 44"><text x="34" y="17" font-family="Raleway,sans-serif" font-weight="700" font-size="18" fill="var(--teal)" text-anchor="middle">$</text><path d="M4 34c8-8 16-10 24-6h12c3 0 3 4 0 4H26M4 40c8-4 14-2 22-2 8 0 16-6 24-14 2-2 0-5-3-3l-9 7" fill="var(--teal)" stroke="var(--teal)" stroke-width="2" stroke-linejoin="round"/></svg></div></div>
    <h3>ACCOUNTS RECEIVABLE</h3>
    <p>Lorem ipsum dolor sit amet,<br>consectetur adipiscing elit, sed do</p>
    <span class="btn">Read More</span>
  </div>
  <div class="service-sep" style="left:866px"></div>
  <div class="service" style="left:868px">
    <div class="service-icon"><div class="inner"><svg width="44" height="44" viewBox="0 0 44 44"><rect x="8" y="6" width="28" height="34" rx="3" fill="none" stroke="var(--teal)" stroke-width="3"/><rect x="13" y="11" width="18" height="7" fill="var(--teal)"/><g fill="var(--teal)"><rect x="13" y="22" width="4" height="4"/><rect x="20" y="22" width="4" height="4"/><rect x="27" y="22" width="4" height="4"/><rect x="13" y="29" width="4" height="4"/><rect x="20" y="29" width="4" height="4"/><rect x="27" y="29" width="4" height="4"/></g></svg></div></div>
    <h3>MANAGEMENT ACCOUNTING</h3>
    <p>Lorem ipsum dolor sit amet,<br>consectetur adipiscing elit, sed do</p>
    <span class="btn">Read More</span>
  </div>
</section>

<section class="testimonials">
  <h2 class="col-title" style="left:101px;top:1416px">Client <span>Testimonials</span></h2>
  <svg class="abs" style="left:545px;top:1448px" width="32" height="14" viewBox="0 0 32 14"><circle cx="7" cy="7" r="5.5" fill="none" stroke="var(--teal)"/><circle cx="24" cy="7" r="5.5" fill="none" stroke="var(--teal)"/><path d="M8.5 4.5 6 7l2.5 2.5M22.5 4.5 25 7l-2.5 2.5" fill="none" stroke="var(--teal)"/></svg>
  <div class="divider" style="left:101px;width:476px;top:1467px"><div class="dots" style="left:0;transform:none;padding:0 10px 0 0;background:var(--white)"><i></i><i class="on"></i><i></i></div></div>
  <div class="quote-card">
    <span class="quote-mark" style="left:18px;top:14px">“</span>
    <p>Lorem ipsum dolor sit amet consetug e sed diay nibh euismodl tincidunt ut laoreet dolore magam er vol wisi enim ad minim veniam quis nostrud exerci tationorem ipsum dolor sit ametee sed diammmy nibh euismd tincidunt ut laoreet dolore magna aliqur volpatl tiidunt ut laoreet dolore magna aliqur volpatl Lorem ipsum dolor sit amet consetug e sed diay nibh euismodl tincidunt ut laoreet dolore magam er vol<span class="quote-close">”</span></p>
  </div>
  <svg class="abs" style="left:480px;top:1746px" width="90" height="30" viewBox="0 0 90 30"><path d="M0 1h80L10 28z" fill="#fafafa"/><path d="M10 28 0 1M10 28 80 1" stroke="#e3e3e3" fill="none"/></svg>
  <div class="avatar"><div role="img" aria-label="Portrait photo of the client giving the testimonial"></div></div>
  <div class="client-name">Mr.Elias Marrow</div>

  <div class="v-dash"></div>

  <h2 class="col-title" style="left:758px;top:1416px">Quick <span>Contact</span></h2>
  <div class="divider" style="left:758px;width:341px;top:1467px"><div class="dots" style="left:0;transform:none;padding:0 10px 0 0;background:var(--white)"><i></i><i class="on"></i><i></i></div></div>
  <div class="field" style="top:1520px">Name</div>
  <div class="field" style="top:1562px">Email</div>
  <div class="field" style="top:1605px">Phone</div>
  <div class="field" style="top:1647px">Contry</div>
  <div class="field" style="top:1690px;height:87px">Comment</div>
  <div class="btn" style="left:758px;top:1787px;width:111px;height:34px;line-height:34px">Submit</div>
</section>

<section class="partners">
  <div style="position:absolute;left:0;top:0;width:1200px;height:1px;background:#d8ecf3"></div>
  <h2 class="section-title" style="top:38px">Our <span>Partners</span></h2>
  <div class="divider" style="left:502px;width:196px;top:88px"><div class="dots" style="background:var(--partner-bg)"><i></i><i class="on"></i><i></i></div></div>
  <svg class="abs" style="left:58px;top:172px" width="20" height="36" viewBox="0 0 20 36"><path d="M17 2 3 18l14 16" fill="none" stroke="#ddd" stroke-width="4"/></svg>
  <svg class="abs" style="left:1122px;top:172px" width="20" height="36" viewBox="0 0 20 36"><path d="M3 2l14 16L3 34" fill="none" stroke="#ddd" stroke-width="4"/></svg>
  <div class="partner" style="left:101px"><div class="badge"></div></div>
  <div class="partner" style="left:304px"><div class="badge"></div></div>
  <div class="partner" style="left:510px"><div class="badge"></div></div>
  <div class="partner" style="left:715px"><div class="badge"></div></div>
  <div class="partner" style="left:920px"><div class="badge"></div></div>
</section>

<footer class="footer">
  <h4 style="left:101px;width:112px">Quick Links</h4>
  <ul class="quick-links" style="left:101px;top:67px">
    <li>Home</li><li>About Us</li><li>Services</li><li>Experience</li><li>Resources</li><li>Contact Us</li>
  </ul>
  <div class="f-sep" style="left:250px"></div>

  <h4 style="left:292px;width:193px">Contact Detail</h4>
  <div class="text" style="left:292px;top:67px;width:200px"><b style="color:#fff">401, Dornaby Bookkeeping</b><br>Lorem ipsum dolor sitak amet,<br>conse.</div>
  <div class="text" style="left:292px;top:141px;display:flex;align-items:center;gap:8px"><svg width="12" height="12" viewBox="0 0 12 12"><path d="M2 1c0 5 4 9 9 9l.5-2-2.5-1-1 1C6.5 7.5 4.5 5.5 4 4.5l1-1L4 1z" fill="var(--sky)"/></svg>+123 456 7890</div>
  <div class="text" style="left:292px;top:166px;display:flex;align-items:center;gap:8px"><svg width="12" height="10" viewBox="0 0 12 10"><rect width="12" height="9" fill="var(--sky)"/><path d="M0 0l6 5 6-5" stroke="#333" fill="none"/></svg>info@dornabybooks.net</div>
  <div class="f-sep" style="left:551px"></div>

  <h4 style="left:613px;width:250px">Newsletter Signup</h4>
  <div class="text" style="left:613px;top:66px;width:140px">Get the latest updates by entering your email address</div>
  <div class="newsletter-art" role="img" aria-label="Small paper plane illustration"></div>
  <svg class="abs" style="left:620px;top:158px" width="14" height="12" viewBox="0 0 14 12"><rect y="1" width="14" height="10" fill="#999"/><path d="M0 1l7 5 7-5" stroke="#fff" fill="none"/></svg>
  <div class="newsletter-input">Enter your email</div>
  <div class="newsletter-btn">SUBSCRIBE</div>
  <div class="f-sep" style="left:927px"></div>

  <h4 style="left:992px;width:106px">Follow Us</h4>
  <ul class="social" style="top:66px">
    <li><i style="border-radius:50%"></i>FRIENDWALL</li>
    <li><i style="border-radius:50%"></i>CHIRPLINE</li>
    <li><i style="border-radius:50%"></i>FRIENDWALL</li>
    <li><i></i>RSS FEED</li>
  </ul>
</footer>

<div class="bottom-bar">
  <span class="abs" style="left:101px;top:16px">Copyright © 2016 Dornaby Bookkeeping. All Rights Reserved</span>
  <span class="abs" style="left:859px;top:16px">Terms &amp; Conditions</span>
  <span class="abs" style="left:991px;top:16px">|</span>
  <span class="abs" style="left:1014px;top:16px">Privacy Policy</span>
</div>

</body>
</html>
```